Business Card Design

We are a company that provides stump grinding services for residential and commercial clients. Looking for a simple business card design that may have some type of graphic on the card that will tie in with the Tamsen name(Grizzly Bear, Paw Print, etc) . Possibly some foliage wrapping around part of the card? Would like to have a simple design that stands out because it is unique. We are working on getting the website set up and there is a simple graphic on the top of the page that came to mind when I mentioned the leaves.

Industry/Entity Type

Business

Contact Information for Business Card

Tamsen Stump Grinding 303-257-4788KodiakStumps.Com

Font styles to use
Serif

Requirements
Must have
• Business name
• Website Address
• Phone Number
Nice to have
• Graphics that would be associated with a Tamsen bear.
Should not have
• Nothing frilly

```html
<!DOCTYPE html>
<html lang="en">
<head>
<meta charset="utf-8">
<title>Tamsen Stump Grinding – Business Cards</title>
<link rel="stylesheet" href="https://fonts.googleapis.com/css2?family=Josefin+Sans:wght@400;600&family=Open+Sans:wght@400&display=swap">
<style>
  :root {
    --stage: #ecebea;
    --blue-deep: #0a84ff;
    --blue-light: #5aaaf8;
    --grey-dark: #6e6e6e;
    --grey-light: #8f8f8f;
    --white: #ffffff;
    --card-shadow: 0 6px 18px rgba(0,0,0,0.18);
  }
  * { margin: 0; padding: 0; box-sizing: border-box; }
  html, body { width: 1200px; height: 900px; overflow: hidden; }
  body { background: var(--stage); position: relative; font-family: "Josefin Sans", sans-serif; }

  .card { position: absolute; overflow: hidden; box-shadow: var(--card-shadow); }

  /* Front */
  .card-front { left: 238px; top: 62px; width: 555px; height: 343px; }
  .card-front .backdrop { position: absolute; inset: 0; }
  .front-name {
    position: absolute; left: 32px; top: 176px;
    color: var(--white); font-weight: 600; font-size: 27px; letter-spacing: 0.5px;
    line-height: 1;
  }
  .front-tagline {
    position: absolute; left: 34px; top: 212px;
    color: var(--white); font-size: 15px; letter-spacing: 12.4px; line-height: 1;
  }
  .contact {
    position: absolute; left: 358px; top: 240px; list-style: none;
    color: var(--white); font-family: "Open Sans", sans-serif; font-size: 16px;
  }
  .contact li { display: flex; align-items: center; gap: 8px; height: 25px; }
  .contact svg { width: 13px; height: 13px; fill: var(--white); }

  /* Back */
  .card-back {
    left: 457px; top: 518px; width: 560px; height: 342px;
    background: linear-gradient(100deg, var(--blue-deep) 0%, var(--blue-light) 100%);
  }
  .brand-mark {
    position: absolute; left: 100px; top: 122px; width: 100px; height: 100px;
    border-radius: 50%; background: var(--white);
  }
  .back-name {
    position: absolute; left: 211px; top: 144px;
    color: var(--white); font-weight: 600; font-size: 33px; letter-spacing: 0.5px; line-height: 1;
  }
  .back-tagline {
    position: absolute; left: 213px; top: 186px;
    color: var(--white); font-size: 17px; letter-spacing: 14.6px; line-height: 1;
  }
</style>
</head>
<body>

<section class="card card-front" aria-label="Business card front">
  <svg class="backdrop" viewBox="0 0 555 343" width="555" height="343" aria-hidden="true">
    <defs>
      <linearGradient id="frontBlue" x1="0" y1="0" x2="1" y2="0">
        <stop offset="0" stop-color="#0a84ff"/>
        <stop offset="1" stop-color="#4ea2f6"/>
      </linearGradient>
      <linearGradient id="frontGrey" x1="0" y1="0" x2="0" y2="1">
        <stop offset="0" stop-color="#8f8f8f"/>
        <stop offset="1" stop-color="#6a6a6a"/>
      </linearGradient>
    </defs>
    <rect width="555" height="343" fill="url(#frontBlue)"/>
    <path d="M300,0 C250,80 250,140 290,200 C320,250 300,300 288,343 L555,343 L555,0 Z" fill="url(#frontGrey)"/>
    <path d="M300,0 C250,80 250,140 290,200 C320,250 300,300 288,343" fill="none" stroke="#ffffff" stroke-width="44"/>
  </svg>

  <h1 class="front-name">TAMSEN STUMP</h1>
  <p class="front-tagline">GRINDING</p>

  <ul class="contact">
    <li>
      <svg viewBox="0 0 24 24"><path d="M3 9c0-3 4-5 9-5s9 2 9 5v2h-5V8.5c-1-.5-2.5-.8-4-.8s-3 .3-4 .8V11H3z M6 13h12l2 7H4z"/></svg>
      303-555-0146
    </li>
    <li>
      <svg viewBox="0 0 24 24"><path d="M10 14a4 4 0 0 1 0-5.6l3-3a4 4 0 0 1 5.6 5.6l-1.5 1.5-1.4-1.4 1.5-1.5a2 2 0 0 0-2.8-2.8l-3 3a2 2 0 0 0 0 2.8z M14 10a4 4 0 0 1 0 5.6l-3 3a4 4 0 0 1-5.6-5.6l1.5-1.5 1.4 1.4-1.5 1.5a2 2 0 0 0 2.8 2.8l3-3a2 2 0 0 0 0-2.8z"/></svg>
      TamsenStumps.Com
    </li>
  </ul>
</section>

<section class="card card-back" aria-label="Business card back">
  <div class="brand-mark" aria-hidden="true"></div>
  <h2 class="back-name">TAMSEN STUMP</h2>
  <p class="back-tagline">GRINDING</p>
</section>

</body>
</html>
```